Business Card Design

Looking for business card designs for a new business. there will be two cards of the same design (both lots of information below in contact info). We would like the logo diagonally across the card with the information split above and below the logo similar to sketch. happy to look at similar alternatives
Please use same colours as in logo design

Industry/Entity Type

Business

Contact Information for Business Card

Dwight Halloran
mob - 0491 738 204
ph - 02 6148 3920
fax - 02 6148 3975
email - dwight@kestrelbeams.com.au
14 Larkmoor Road, Corvale WA 6741

Colin Marchetti
mob - 0438 912 557
ph - 02 6148 3920
fax - 02 6148 3975
email - colin@kestrelbeams.com.au

```html
<!DOCTYPE html>
<html lang="en">
<head>
<meta charset="utf-8">
<title>Kestrel Beams – Business Cards</title>
<link href="https://fonts.googleapis.com/css2?family=Source+Sans+3:wght@400;600;700&display=swap" rel="stylesheet">
<style>
  :root {
    --teal: #0f7f7b;
    --ink: #1a1a1a;
    --paper: #ffffff;
    --night: #000000;
    --backdrop: #ece8e2;
    --text-grey: #2b2b2b;
  }
  * { box-sizing: border-box; margin: 0; padding: 0; }
  html, body {
    width: 1146px; height: 1200px; overflow: hidden;
    background: var(--backdrop);
    font-family: "Source Sans 3", "Myriad Pro", Arial, sans-serif;
  }
  .canvas { position: relative; width: 1146px; height: 1200px; }

  .card { position: absolute; width: 940px; height: 538px; }
  .card--front {
    left: 184px; top: 32px;
    background: var(--paper);
    border: 1px solid #cfcfcf;
    box-shadow: 0 3px 8px rgba(0,0,0,.18);
  }
  .card--back {
    left: 43px; top: 624px;
    background: var(--night);
    box-shadow: 0 3px 8px rgba(0,0,0,.25);
  }

  .side-tab {
    position: absolute; top: 97px; width: 20px; height: 360px;
    background: var(--teal);
  }
  .side-tab--left { left: 0; border-radius: 0 14px 14px 0; }
  .side-tab--right { right: 0; border-radius: 14px 0 0 14px; }

  .brand {
    position: absolute; left: 0; right: 0;
    display: flex; align-items: center; justify-content: center; gap: 18px;
    font-weight: 700; letter-spacing: 0.5px; line-height: 1;
  }
  .brand__mark { display: block; flex: none; }
  .card--front .brand { top: 110px; font-size: 78px; color: var(--ink); }
  .card--front .brand__mark { width: 62px; height: 62px; background: var(--teal); }
  .card--back .brand { top: 220px; font-size: 100px; color: var(--teal); }
  .card--back .brand__mark { width: 80px; height: 80px; background: var(--paper); }

  .contact { position: absolute; left: 0; right: 0; text-align: center; color: var(--text-grey); line-height: 1.2; }
  .contact__name { top: 266px; font-size: 29px; font-weight: 700; color: var(--teal); }
  .contact__phones {
    top: 344px; font-size: 22px;
    display: flex; justify-content: center; align-items: center; gap: 8px;
  }
  .contact__phones .item { display: inline-flex; align-items: center; gap: 4px; }
  .contact__email {
    top: 386px; font-size: 22px;
    display: flex; justify-content: center; align-items: center; gap: 6px;
  }
  .contact__address { top: 446px; font-size: 22px; }
  .icon { width: 18px; height: 18px; fill: var(--teal); flex: none; }

  .web-address {
    position: absolute; left: 0; right: 0; top: 428px;
    text-align: center; color: var(--paper);
    font-size: 27px; letter-spacing: 3px; font-weight: 400; line-height: 1.2;
  }
  .web-address strong { font-weight: 600; }
</style>
</head>
<body>
<main class="canvas">

  <section class="card card--front" aria-label="Business card front">
    <span class="side-tab side-tab--left"></span>
    <span class="side-tab side-tab--right"></span>

    <div class="brand"><span class="brand__mark"></span><span>Kestrel Beams</span></div>

    <p class="contact contact__name">Colin Marchetti</p>

    <p class="contact contact__phones">
      <span class="item">
        <svg class="icon" viewBox="0 0 24 24" aria-hidden="true"><path d="M6.6 10.8a15.2 15.2 0 0 0 6.6 6.6l2.2-2.2a1 1 0 0 1 1-.25 11.4 11.4 0 0 0 3.6.57 1 1 0 0 1 1 1V20a1 1 0 0 1-1 1A17 17 0 0 1 3 4a1 1 0 0 1 1-1h3.5a1 1 0 0 1 1 1c0 1.25.2 2.45.57 3.57a1 1 0 0 1-.25 1z"/></svg>
        02 6148 3920
      </span>
      <span class="item">
        <svg class="icon" viewBox="0 0 24 24" aria-hidden="true"><path d="M8 1h8a2 2 0 0 1 2 2v18a2 2 0 0 1-2 2H8a2 2 0 0 1-2-2V3a2 2 0 0 1 2-2zm0 3v12h8V4zm4 14a1.4 1.4 0 1 0 0 2.8A1.4 1.4 0 0 0 12 18z"/></svg>
        0438 912 557
      </span>
      <span class="item">
        <svg class="icon" viewBox="0 0 24 24" aria-hidden="true"><path d="M7 3h10v5H7zM4 9h16a2 2 0 0 1 2 2v7h-4v3H6v-3H2v-7a2 2 0 0 1 2-2zm4 7v3h8v-3z"/></svg>
        02 6148 3975
      </span>
    </p>

    <p class="contact contact__email">
      <svg class="icon" viewBox="0 0 24 24" aria-hidden="true"><path d="M2 9l10-6 10 6v11a1 1 0 0 1-1 1H3a1 1 0 0 1-1-1zm2 1.2V19h16v-8.8l-8 5z"/></svg>
      colin@kestrelbeams.com.au
    </p>

    <p class="contact contact__address">14 Larkmoor Road, Corvale WA 6741</p>
  </section>

  <section class="card card--back" aria-label="Business card back">
    <div class="brand"><span class="brand__mark"></span><span>Kestrel Beams</span></div>
    <p class="web-address">www.<strong>kestrelbeams</strong>.com.au</p>
  </section>

</main>
</body>
</html>
```